Visitenkarten für Mentorin für Frauen
Zielgruppe
Ich bin Mentorin für Frauen (30-50 Jahre alt), die ihre Berufung endlich finden möchten und sich nach mehr Energie und Sinn sehnen. Ich helfe ihnen mit meiner (Name fehtl noch)-Methode ihren Seelenweg zu finden und zu gehen, sodass sie vor Energie übersprudeln und mit einem Leuchten in den Augen ein Leben in Fluss und Fülle kreieren.
Sie sind nicht unglücklich, aber es fehtl ihnen was, das sie wirklich erfüllt.
Stichwörter: Numerologie, Human Design, Seelenweg, Berufung, Lebensaufgabe, erfüllt sein- endlich die Leere füllen, Freiheit, Selbstbestimmt, Selbstliebe, Potentialentfaltung, Transformation
meine core story:
Mit Freude, unglaublicher Energie und einem Strahlen in den Augen schon vor dem Wecker aufzustehen, war für mich früher undenkbar. Ich konnte mir nicht vorstellen, wie sich Leute auf den Montag freuen konnten.
Dabei hätte mich nicht als unglücklich bezeichnet, aber es fehlt einfach etwas, ich hatte eine innere Leere und eine Sehnsucht nach dem Sinn in meinem Lebe, wollte so geliebt werden wie ich bin und mich auch so zeigen können. Ich weiß wie es ist sich klein, unsicher zu fühlen und nicht zu wissen woher das kommt. Ich habe es einfach nicht für möglich gehalten, dass diese innere Leere so leicht zu füllen ist und Freude, Spaß, Selbstbewusstseein und Leichtigkeit in allen Bereichen mit sich bringt.
Weil ich selbst diesen Weg gegangen bin und weil ich weiß, dass es nichts erfüllenderes gibt als das schlummernde Potential zu erwecken, begleite ich Frauen dabei ihren Seelenweg zu finden und zu gehen.
Dadurch dass sie genau wissen, was ihre Gaben sind und was ihre Seele glücklich macht, haben sie Spaß und Freude, gerade auch in den alltäglichen Dingen. Sie führen ein selbstbestimmtes Leben, lieben sich selbst und zeigen sich so wie sie sind.Die gigantische Energie die dadurch in ihnen frei wird, lässt sie die bisherigen Grenzen überwinden. Sie tun was sie erfüllt, o..
Aufgabenstellung
weiblich, geschwungen, weich: beinhalten solls:
Marlene Wittberg
Mentorin für Powerfrauen
(Lebe deine Berufung)--> da bin ich mir nicht ganz sicher ob das gut aussehn wird oder zuviel wird
falls relevant habe ich bisher folgende Schriftarten verwendet: Canva Sans und Tan mon cheri
ist aber kein muss

```html
<!DOCTYPE html>
<html lang="de">
<head>
<meta charset="utf-8">
<title>Marlene Wittberg – Mentorin für Powerfrauen</title>
<link rel="stylesheet" href="https://fonts.googleapis.com/css2?family=Amatic+SC:wght@700&family=Josefin+Sans:wght@300&display=swap">
<style>
  :root {
    --blush-top: #f3c3c0;
    --peach-bottom: #fad3b0;
    --ink: #3b3a39;
    --gold: #a08a55;
    --glitter: rgba(214, 178, 92, 0.35);
  }
  html, body {
    margin: 0;
    padding: 0;
    overflow: hidden;
  }
  .card {
    position: relative;
    width: 777px;
    height: 1200px;
    overflow: hidden;
    background: linear-gradient(180deg, var(--blush-top) 0%, #f6cbb8 50%, var(--peach-bottom) 100%);
  }
  .glitter-field {
    position: absolute;
    left: 0;
    top: 520px;
    width: 777px;
    height: 680px;
    background:
      radial-gradient(ellipse 60% 40% at 55% 25%, var(--glitter), transparent 70%),
      radial-gradient(ellipse 45% 35% at 25% 75%, rgba(214,178,92,0.2), transparent 70%);
  }
  .name {
    position: absolute;
    left: 0;
    width: 777px;
    margin: 0;
    text-align: center;
    font-family: "Amatic SC", cursive;
    font-weight: 700;
    font-size: 190px;
    line-height: 1;
    letter-spacing: 6px;
  }
  .name--first {
    top: 100px;
    color: var(--ink);
  }
  .name--last {
    top: 318px;
    color: var(--gold);
  }
  .divider {
    position: absolute;
    left: 0;
    top: 0;
  }
  .tagline {
    position: absolute;
    left: 140px;
    top: 745px;
    margin: 0;
    font-family: "Josefin Sans", sans-serif;
    font-weight: 300;
    font-size: 58px;
    line-height: 1.45;
    color: var(--ink);
    text-transform: uppercase;
  }
</style>
</head>
<body>
  <main class="card">
    <div class="glitter-field" role="img" aria-label="Verstreute goldene Glitzerpartikel"></div>

    <h1 class="name name--first">Marlene</h1>
    <p class="name name--last">Wittberg</p>

    <svg class="divider" width="777" height="1200" viewBox="0 0 777 1200" aria-hidden="true">
      <line x1="0" y1="710" x2="777" y2="557" stroke="var(--gold)" stroke-width="9"/>
      <line x1="0" y1="1119" x2="777" y2="975" stroke="var(--gold)" stroke-width="9"/>
    </svg>

    <p class="tagline">Mentorin für<br>Powerfrauen</p>
  </main>
</body>
</html>
```